Wordpress Design Project for Bankruptcy Law Office in San Francisco

our current website: www.dorvanelilaw-example.com

we would like to re-design it for wordpress to make it faster and a bit more modern.

content should be similar to what we have there right now but also we do family law

please include logo for law office:

Law Office of Marta K. Dolvenidze

Thank you.
Updates

please see attached word document with logos that we like as an example.

we do tend to like color red.  darker red.

Please submit your design variations and logo as soon as possible.   We would like to go over them and make our decision

Reason: Please create couple of more variations of logo for your design, so we can make our decision what we like the most. Please see word doc for samples: Text: Law Office Of Marta K. Dolvenidze

Reason: final touches

Target Market(s)

bankruptcy and family law clients

Industry/Entity Type

Family Law

Requirements
Must have
• see examples of law sites
http://promo.lexorbin-example.com/testimonials

- new logo: Law Office of Marta K. Dolvenidze
- client intake form
- blog
- contact us form

Nice to have
• - map
- red color
- on the front page a nice photo of SF or a happy family

```html
<!DOCTYPE html>
<html lang="en">
<head>
<meta charset="utf-8">
<title>Law Office of Marta K. Dolvenidze</title>
<link href="https://fonts.googleapis.com/css2?family=Open+Sans:wght@400;600;700&family=Lato:wght@400;700;900&display=swap" rel="stylesheet">
<style>
:root{
  --admin:#222222;
  --admin-text:#dddddd;
  --maroon:#2b0c07;
  --green:#8cc63e;
  --green-dark:#78ad30;
  --white:#ffffff;
  --text:#6b6b6b;
  --heading:#333333;
  --nav:#222222;
  --rule:#7a4a40;
  --footer:#efefec;
  --footer-line:#dcdcd8;
  --link:#3a78c3;
  --muted:#9a9a9a;
  --field:#cfcfcf;
}
*{box-sizing:border-box;margin:0;padding:0}
html,body{width:667px;height:1200px;overflow:hidden}
body{position:relative;background:var(--maroon);font-family:'Open Sans',Arial,sans-serif;color:var(--text)}
.abs{position:absolute}

/* admin bar */
.admin-bar{left:0;top:0;width:667px;height:18px;background:var(--admin);color:var(--admin-text);font-size:8.5px;display:flex;align-items:center}
.admin-bar .item{padding:0 9px;line-height:18px;white-space:nowrap}
.admin-bar .dot{width:12px;height:12px;border-radius:50%;background:#888;margin:0 6px 0 7px}
.admin-bar .howdy{margin-left:auto;display:flex;align-items:center;gap:5px;padding-right:6px}
.admin-bar .avatar{width:12px;height:12px;background:#999}

/* header */
.logo-art{left:23px;top:22px;width:390px;height:143px;background:linear-gradient(100deg,#5c140c 0%,#3a0a06 45%,#6a3a14 62%,#2b0c07 100%)}
.logo-name{left:36px;top:48px;font-family:'Lato',sans-serif;font-weight:400;font-size:25px;color:#e9e3dc;line-height:1}
.logo-sub{left:88px;top:84px;font-family:'Lato',sans-serif;font-weight:400;font-size:13px;color:#e9e3dc;letter-spacing:.5px}
.call-box{left:413px;top:18px;width:82px;height:70px;background:var(--green);color:var(--white);font-weight:700;font-size:8px;line-height:15px;padding:10px 10px}
.search{left:499px;top:14px;width:146px;height:16px;background:var(--white);font-size:8px;color:#aaa;padding:2px 5px}

/* nav */
.main-nav{left:23px;top:200px;width:622px;height:25px;background:var(--nav);display:flex;align-items:center;padding-left:7px;gap:14px}
.main-nav a{color:var(--white);font-size:7.5px;font-weight:600;text-decoration:none;text-transform:uppercase;display:flex;align-items:flex-start;gap:3px}
.main-nav .caret{width:7px;height:7px;background:#e8e8e8;margin-top:-4px}

/* welcome */
.welcome-icon{left:24px;top:246px}
.welcome-title{left:47px;top:245px;width:598px;height:16px;background:var(--white);font-size:11px;font-weight:400;color:var(--heading);line-height:16px;padding-left:4px;text-transform:uppercase}
.panel{background:var(--white);border-radius:2px;font-size:8.5px;line-height:15.3px;padding:2px 2px}
.welcome-text{left:23px;top:271px;width:622px;height:108px}
.rule{left:23px;width:622px;height:1px;background:var(--rule)}

/* service cards */
.card{width:146px;background:var(--white);border-radius:2px;padding:16px 17px 0}
.card h3{font-family:'Lato',sans-serif;font-weight:900;font-size:7.5px;letter-spacing:1px;color:var(--heading);text-transform:uppercase;line-height:12px;margin-bottom:4px}
.card p{border:1px solid #e2e2e2;font-size:8.2px;line-height:12.3px;padding:0 2px;margin-bottom:10px}
.btn{display:inline-block;background:var(--green);color:var(--white);font-weight:700;font-size:7px;text-transform:uppercase;padding:9px 10px;border-bottom:2px solid var(--green-dark)}

/* testimonials */
.label{left:23px;top:666px;font-family:'Lato',sans-serif;font-weight:700;font-size:7.5px;letter-spacing:1.5px;color:#5a3a34;text-transform:uppercase}
.testi-title{left:23px;top:687px;width:622px;height:16px;font-size:8.3px;line-height:12px}
.testi-text{left:23px;top:713px;width:622px;height:92px}

/* footer */
.footer{left:0;top:825px;width:667px;height:375px;background:var(--footer)}
.col{top:848px;width:146px}
.col h4{font-family:'Lato',sans-serif;font-weight:900;font-size:7.5px;letter-spacing:1px;color:#333;text-transform:uppercase;margin-bottom:10px}
.snip-sub{font-size:9px;color:#333;margin-bottom:5px}
.snip-box{background:var(--white);border:1px solid #e6e6e6;font-size:8.2px;line-height:15px;padding:2px 3px;height:123px}
.arrows{left:146px;top:848px;display:flex;gap:2px}
.arrows span{width:10px;height:10px;border-radius:50%;background:#bdbdbd}
.posts li{list-style:none;font-size:8.5px;color:var(--link);line-height:17px;padding-left:7px;position:relative}
.posts li:before{content:"›";position:absolute;left:0;color:#999}
.tweet{font-size:8.2px;line-height:12.3px;margin-bottom:8px}
.tweet a{color:var(--link);text-decoration:none;display:block}
.tweet small{display:block;font-size:7px;color:var(--muted);margin-top:1px}
.follow{border:1px solid #e2e2e2;background:var(--white);font-size:8.5px;color:var(--green-dark);padding:2px 3px}
.form label{display:block;font-size:8.2px;color:#444;margin-bottom:2px}
.form .field{height:14px;background:var(--white);border:1px solid var(--field);margin-bottom:7px}
.form .area{height:127px}
.form .btn{padding:7px 8px}
.footer-rule{left:23px;top:1157px;width:622px;height:1px;background:var(--footer-line)}
.copyright{left:23px;top:1172px;font-size:7.5px;color:var(--muted)}
</style>
</head>
<body>

<div class="abs admin-bar">
  <span class="dot"></span>
  <span class="item">Law Office of Marta K. Dolvenidze</span>
  <span class="item">
    <svg width="10" height="9" viewBox="0 0 10 9"><path d="M1 1h8v5H5L3 8V6H1z" fill="#aaa"/></svg>
  </span>
  <span class="item">+ New</span>
  <span class="item">Edit Page</span>
  <span class="howdy">Howdy, hollisv <span class="avatar"></span></span>
</div>

<div class="abs logo-art" role="img" aria-label="Scales of justice and gavel on a dark red desk"></div>
<div class="abs logo-name">Marta K. Dolvenidze</div>
<div class="abs logo-sub">LAW OFFICE</div>

<div class="abs call-box">FEEL FREE<br>TO CALL US AT<br>(415) 555-0182</div>
<div class="abs search">Search ...</div>

<nav class="abs main-nav">
  <a href="#">About <span class="caret"></span></a>
  <a href="#">Areas of Practice <span class="caret"></span></a>
  <a href="#">Resources <span class="caret"></span></a>
  <a href="#">Blog <span class="caret"></span></a>
  <a href="#">FAQ</a>
  <a href="#">Contact Us</a>
</nav>

<svg class="abs welcome-icon" width="18" height="14" viewBox="0 0 18 14" aria-hidden="true">
  <path d="M1 2l5-1.5 6 2 5-1.5v11l-5 1.5-6-2-5 1.5z M6 0.5v11 M12 2.5v11" fill="none" stroke="#c9b46a" stroke-width="1.4"/>
</svg>
<h1 class="abs welcome-title">Welcome to DK Law 220 – Complete Bankruptcy Information</h1>
<div class="abs panel welcome-text">The Law Offices of Marta K. Dolvenidze is a consumer law office dedicated to consumer protection and zealously defending the rights of our clients. We offer the big firm quality legal representation with a small firm individualized attention to each client. Our office offers services in: all types of consumer bankruptcy filings, i.e. Chapter 7, Chapter 13, Chapter 11, negotiating a settlement of your debts, assisting you in the defense of collection litigation and defending you against foreclosure. Please review our site and see what we may be able to offer you. Feel free to call us at (415) 555-0182 or use our free case evaluation form. Speak to a Lawyer Unlike some other law firms, when you call the Law Office of Marta K. Dolvenidze you will speak to an actual attorney. Not a paralegal or assistant. And even after retaining our office you will still speak to an attorney unlike other firms where you cannot get a hold of your attorney after several attempts.</div>

<div class="abs rule" style="top:398px"></div>

<div class="abs card" style="left:23px;top:420px;height:203px">
  <h3>Debt Relief</h3>
  <p>Lorem ipsum dolor sit amet, consectetur adipisicing elit, sed do eiusmod tempor incididunt ut labore et dolore magna aliqua. Ut enim ad minim veniam, quis nostrud exercitation ullamco laboris nisi ut aliquip ex ea commodo consequat.</p>
  <a class="btn">Read More</a>
</div>
<div class="abs card" style="left:182px;top:420px;height:178px">
  <h3>Foreclosure Prevention</h3>
  <p>Lorem ipsum dolor sit amet, consectetur adipisicing elit, sed do eiusmod tempor incididunt ut labore et dolore magna aliqua. Ut enim ad minim veniam.</p>
  <a class="btn">Read More</a>
</div>
<div class="abs card" style="left:340px;top:420px;height:165px">
  <h3>Chapter 13</h3>
  <p>An individual with a regular income who is overcome by debts, but believes such debt can be repaid within a reasonable period of time, may file under chapter 13 of the bankruptcy code.</p>
  <a class="btn">Read More</a>
</div>
<div class="abs card" style="left:499px;top:420px;height:190px">
  <h3>Chapter 7</h3>
  <p>Often called the liquidation chapter, or “fresh start,” chapter 7 is used by individuals, families, partnerships, or corporations whose financial difficulties do not allow them to repay all of their debts.</p>
  <a class="btn">Read More</a>
</div>

<div class="abs rule" style="top:645px"></div>

<div class="abs label">Testimonials</div>
<div class="abs panel testi-title">Excellent Bankruptcy Attorney</div>
<div class="abs panel testi-text">During our difficult financial times, we pretty much run out of all the possible options. Last option was bankruptcy and it was very difficult to decide on that and to understand what it is all about. It only took 30min with our consultation with Marta, that we really understood what all those chapters are about and understood our options. Before that chapter 7 or 13 were just numbers. Finally it was more clear what we can keep in bankruptcy solution and what we can't. Marta was very patient and made sure we have all of our questions answered before we went to next step. She also gave us materials to read at home. Once we decided to go for it, Ms. Dolvenidze sent us an online form, that was easy to fill out… from their she took care of everything. At court or any meetings we were explained every step. Once again Thank you very Much!!! Marta is very professional, experienced and understanding attorney.</div>

<footer class="abs footer"></footer>

<div class="abs col" style="left:23px">
  <h4>Snippets Title</h4>
  <div class="snip-sub">Free Case Review</div>
  <div class="snip-box">Fields marked with * are required. Name * Email * Phone &nbsp;Do you own real estate? &nbsp;yes &nbsp;no If yes, are you behind on payments? &nbsp;yes &nbsp;no Do you own an automobile? &nbsp;yes &nbsp;no If yes, are you behind on payments? &nbsp;yes &nbsp;no Do you have any additional …</div>
</div>
<div class="abs arrows"><span></span><span></span></div>

<div class="abs col" style="left:182px">
  <h4>Recent Posts</h4>
  <ul class="posts">
    <li>Hello world!</li>
    <li>The snow party</li>
    <li>Over the hill</li>
    <li>Brokeback Snowy Mountain</li>
    <li>How to jump like a noob?</li>
  </ul>
</div>

<div class="abs col" style="left:340px">
  <h4>Latest Tweets</h4>
  <div class="tweet">Hot off the press! Chirpline buzz surrounding the #LMA's last night racked in nearly 15m Tweets! <small>20 hours ago</small></div>
  <div class="tweet">The #LMA's: A look back via Chirpline <a>http://lnk.example/qr7Tm2</a><small>21 hours ago</small></div>
  <div class="tweet">Bayside Style week is underway #bsw. Here's our blog post <a>http://lnk.example/Hd4kPz</a> and a quick "get started" guide <a>https://lnk.example/Wv9sNe</a><small>1 day ago</small></div>
  <div class="follow">Follow Me →</div>
</div>

<div class="abs col form" style="left:499px">
  <h4>Contact Us Form</h4>
  <label>Name:</label><div class="field"></div>
  <label>Email:</label><div class="field"></div>
  <label>Subject:</label><div class="field"></div>
  <label>Your Message:</label><div class="field area"></div>
  <a class="btn">Submit</a>
</div>

<div class="abs footer-rule"></div>
<div class="abs copyright">© Copyright 2012 Law Office of Marta K. Dolvenidze. All Rights Reserved.</div>

</body>
</html>
```